product development company BRVEMKO LLC business card

We need a business card design for a company based in Texas called 'BRVEMKO LLC'. Our first product is a illuminated portable ice chest that is called ' Copper Harbor coolers'. Copper harbor coolers is trademarked. I would like to have the copper harbor trademark somewhere on the card as well as the BRVEMKO LLC name.

Target Market(s)

outdoor industry

Industry/Entity Type

Business

Contact Information for Business Card

i would like to have BRVEMKO LLC logo larger than the Copper harbor coolers logo.

Font styles to use
Serif
Sans Serif

```html
<!DOCTYPE html>
<html lang="en">
<head>
<meta charset="utf-8">
<title>BRVEMKO LLC – Business Card</title>
<link href="https://fonts.googleapis.com/css2?family=Marcellus&family=Tinos:ital,wght@0,400;0,700;1,400&display=swap" rel="stylesheet">
<style>
  :root{
    --backdrop:#e6e4e0;
    --card-white:#f7f7f7;
    --ink:#111111;
    --ink-soft:#6f6f6f;
    --shadow:rgba(0,0,0,.18);
  }
  *{margin:0;padding:0;box-sizing:border-box}
  html,body{width:1200px;height:780px;overflow:hidden;background:var(--backdrop)}
  .card{
    position:absolute;left:75px;top:90px;width:1050px;height:600px;
    background:linear-gradient(160deg,#ffffff 0%,var(--card-white) 60%,#ececec 100%);
    box-shadow:0 14px 40px var(--shadow);overflow:hidden;
  }
  .card-shapes{position:absolute;inset:0}
  .brand{position:absolute;left:50px;top:120px;width:510px;text-align:center}
  .brand-name{
    font-family:"Marcellus",serif;font-size:92px;letter-spacing:6px;color:var(--ink);line-height:1;
  }
  .brand-suffix{
    display:flex;align-items:center;justify-content:center;gap:18px;margin-top:16px;
    font-family:"Marcellus",serif;font-size:38px;letter-spacing:20px;color:var(--ink);line-height:1;
  }
  .brand-suffix .dots{width:100px;border-top:4px dotted var(--ink)}
  .holder{position:absolute;right:70px;top:50px;text-align:right;font-family:"Tinos",serif}
  .holder-name{font-size:30px;letter-spacing:1px;color:var(--ink)}
  .holder-title{font-size:22px;color:var(--ink-soft);margin-top:2px}
  .product{
    position:absolute;right:70px;top:160px;display:flex;align-items:center;gap:12px;
    font-family:"Tinos",serif;font-weight:700;font-size:30px;color:var(--ink);
  }
  .product-mark{width:26px;height:26px;border-radius:50%;background:var(--ink)}
  .contact{
    position:absolute;left:70px;top:425px;font-family:"Tinos",serif;font-size:25px;line-height:1.38;color:var(--ink);
  }
  .contact-line{display:flex;align-items:center;gap:10px}
  .contact-icon{width:24px;height:24px;background:var(--ink);display:inline-flex;align-items:center;justify-content:center}
  .website{
    position:absolute;right:60px;bottom:40px;font-family:"Tinos",serif;font-size:26px;color:var(--ink);
  }
</style>
</head>
<body>
<div class="card">
  <svg class="card-shapes" width="1050" height="600" viewBox="0 0 1050 600">
    <defs>
      <linearGradient id="bandGrey" x1="0" y1="0" x2="1" y2="1">
        <stop offset="0" stop-color="#bdbdbd"/>
        <stop offset="1" stop-color="#8e8e8e"/>
      </linearGradient>
    </defs>
    <polygon class="band-grey" fill="url(#bandGrey)"
      points="0,395 575,395 645,275 690,275 760,370 830,290 1050,290 1050,600 0,600"/>
    <polygon class="band-black" fill="#111"
      points="0,360 555,360 625,240 690,240 690,275 645,275 575,395 0,395"/>
    <polygon class="band-black-base" fill="#111"
      points="0,585 1050,585 1050,600 0,600"/>
  </svg>

  <div class="brand">
    <div class="brand-name">BRVEMKO</div>
    <div class="brand-suffix"><span class="dots"></span>LLC<span class="dots"></span></div>
  </div>

  <div class="holder">
    <div class="holder-name">DALE MORROW</div>
    <div class="holder-title">Manager</div>
  </div>

  <div class="product"><span class="product-mark"></span>Copper Harbor coolers</div>

  <div class="contact">
    <div>Your Address, 2nd Ste</div>
    <div>Brookfield, Texas 1234</div>
    <div class="contact-line">
      <span class="contact-icon">
        <svg width="16" height="16" viewBox="0 0 16 16"><path d="M4 1h3l1 4-2 1a8 8 0 0 0 4 4l1-2 4 1v3c0 1-1 2-2 2A12 12 0 0 1 2 3c0-1 1-2 2-2z" fill="#fff"/></svg>
      </span>123 456 7890
    </div>
    <div class="contact-line">
      <span class="contact-icon">
        <svg width="16" height="16" viewBox="0 0 16 16"><rect x="1" y="3" width="14" height="10" fill="none" stroke="#fff" stroke-width="1.6"/><path d="M1 3l7 6 7-6" fill="none" stroke="#fff" stroke-width="1.6"/></svg>
      </span>your@yourcompany.com
    </div>
  </div>

  <div class="website">www.yourcompany.com</div>
</div>
</body>
</html>
```